Create American style design suitable for consumers in Europe and America

We need a professional universal neutral design, which can be applied to all personal care tools, regardless of male and female, and the color matching needs to be matched by designers themselves.
Updates

设计质量低

Target Market(s)

Europe and America

Industry/Entity Type

personal care tools

Font styles to use
Serif
Sans Serif
Script

Requirements
Must have
• personal beauty care tool,like nail clipper,tweezer,scissors
Nice to have
• The copywriter plans on the packaging design can be applied to all personal care tools
Should not have
• Not designed for a single product, but for a whole personal care tool

```html
<!DOCTYPE html>
<html lang="en">
<head>
<meta charset="UTF-8">
<title>Velora Care Tools – Hang Card</title>
<link href="https://fonts.googleapis.com/css2?family=Montserrat:wght@700;800&family=Quicksand:wght@500;600&family=Oswald:wght@600&display=swap" rel="stylesheet">
<style>
  :root {
    --stage: #231f20;
    --card: #ffffff;
    --ink: #231f20;
    --gold: #d4ab55;
    --mist: #e4e4e4;
    --steel-dark: #2b2b2d;
    --steel-light: #c9c9cb;
  }
  * { margin: 0; padding: 0; box-sizing: border-box; }
  html, body { width: 1200px; height: 999px; overflow: hidden; background: var(--stage); }
  .stage { position: relative; width: 1200px; height: 999px; }

  .card {
    position: absolute; top: 75px; width: 508px; height: 850px;
    border-radius: 24px; overflow: hidden;
    background:
      radial-gradient(circle at 15% 20%, var(--mist) 0, transparent 22%),
      radial-gradient(circle at 85% 35%, var(--mist) 0, transparent 20%),
      radial-gradient(circle at 20% 65%, var(--mist) 0, transparent 20%),
      radial-gradient(circle at 85% 80%, var(--mist) 0, transparent 22%),
      var(--card);
  }
  .card--front { left: 73px; }
  .card--back { left: 614px; }
  .card__band { position: absolute; left: 0; bottom: 0; width: 100%; height: 14px; background: var(--gold); }

  .hang-hole { position: absolute; left: 196px; top: 28px; width: 118px; height: 42px; }

  .brand { position: absolute; left: 0; width: 100%; top: 88px; text-align: center; color: var(--ink);
    font-family: "Quicksand", sans-serif; font-weight: 500; line-height: 1; }
  .brand__name { display: block; font-size: 62px; letter-spacing: 1px; }
  .brand__tag { display: block; font-size: 21px; letter-spacing: 1px; margin-top: 6px; }

  .product-visual {
    position: absolute; left: 75px; top: 204px; width: 350px; height: 497px; border-radius: 30px;
    background: radial-gradient(ellipse at 50% 40%, var(--steel-light) 0, #8a8a8d 35%, var(--steel-dark) 75%);
    opacity: .85;
  }

  .title { position: absolute; left: 0; width: 100%; text-align: center; color: var(--gold);
    font-family: "Montserrat", sans-serif; font-weight: 800; font-size: 57px; line-height: 1; letter-spacing: -0.5px; }
  .subtitle { position: absolute; left: 0; width: 100%; text-align: center; color: var(--ink);
    font-family: "Quicksand", sans-serif; font-weight: 500; font-size: 28px; line-height: 1; }
  .card--front .title { top: 715px; }
  .card--front .subtitle { top: 778px; }
  .card--back .title { top: 209px; }
  .card--back .subtitle { top: 278px; }

  .description { position: absolute; left: 49px; top: 322px; width: 406px; color: var(--ink);
    font-family: "Quicksand", sans-serif; font-weight: 500; font-size: 15.6px; line-height: 20px;
    text-align: justify; text-align-last: center; hyphens: manual; }

  .badge { position: absolute; width: 96px; height: 96px; border-radius: 50%; border: 1.5px solid var(--gold);
    background: var(--card); display: flex; align-items: center; justify-content: center; text-align: center;
    font-family: "Oswald", sans-serif; font-weight: 600; font-size: 16px; line-height: 19px; color: var(--ink); }
  .badge--steel { left: 136px; top: 583px; }
  .badge--promise { left: 271px; top: 582px; }

  .contact { position: absolute; left: 0; width: 100%; top: 707px; text-align: center;
    font-family: "Montserrat", sans-serif; font-weight: 700; color: var(--ink); }
  .contact__heading { color: var(--gold); font-size: 18.5px; line-height: 24px; }
  .contact__line { font-size: 18.5px; line-height: 25.5px; }
</style>
</head>
<body>
<main class="stage">

  <section class="card card--front">
    <svg class="hang-hole" viewBox="0 0 118 42" aria-hidden="true">
      <circle cx="59" cy="17" r="17" fill="#231f20"/>
      <rect x="0" y="14" width="118" height="27" rx="13.5" fill="#231f20"/>
    </svg>
    <div class="brand"><span class="brand__name">Velora</span><span class="brand__tag">Care Tools</span></div>
    <div class="product-visual" role="img" aria-label="Product photo: stainless steel cuticle nipper with black speckled handles"></div>
    <h1 class="title">NAIL CLIPPER</h1>
    <p class="subtitle">Personal beauty care tool</p>
    <div class="card__band"></div>
  </section>

  <section class="card card--back">
    <svg class="hang-hole" viewBox="0 0 118 42" aria-hidden="true">
      <circle cx="59" cy="17" r="17" fill="#231f20"/>
      <rect x="0" y="14" width="118" height="27" rx="13.5" fill="#231f20"/>
    </svg>
    <div class="brand"><span class="brand__name">Velora</span><span class="brand__tag">Care Tools</span></div>
    <h2 class="title">NAIL CLIPPER</h2>
    <p class="subtitle">Personal beauty care tool</p>
    <p class="description">Lorem Ipsum is simply dummy text of the printing and typesetting industry. Lorem Ipsum has been the indus&shy;try's standard dummy text ever since the 1500s, when an unknown printer took a galley of type and scrambled it to make a type specimen book. It has survived not only five centuries, but also the leap into electronic typesetting, remaining essentially unchanged. It was popularised in the 1960s with the release of Typeset sheets containing Lorem Ipsum passages, and more recently with desktop publishing software like Folio Layout including ver&shy;sions of Lorem Ipsum.</p>
    <div class="badge badge--steel">High<br>Quality<br>Stainless<br>Steel</div>
    <div class="badge badge--promise">100%<br>Satisfaction<br>Guatanteed</div>
    <div class="contact">
      <p class="contact__heading">ANY QUESTIONS? CONTACT US</p>
      <p class="contact__line">PH: (123) 456-7890</p>
      <p class="contact__line">E: contact@emailaddress.com</p>
      <p class="contact__line">W: www.websiteaddress.com</p>
    </div>
    <div class="card__band"></div>
  </section>

</main>
</body>
</html>
```